A website where experts collaborate on your project

I am building a new website where experts (yes, like designers) collaborate on projects with the project owner. More minds = more collaboration = better end product. Please see Pelmora(dot)com for a quick landing page I created for collaborating on presentations (although there will be many project types offered)

I am looking for a DESIGNER LONG TERM, but for now, just need initial mock ups to show the web programmers.

I have 21 Word documents loosely designed, what I would like to see here is a theme. Please DO NOT GO OFF WHAT YOU CURRENTLY SEE AT PELMORA. What is up now is only a quick landing page.

You can view a Word doc of the homepage here:
https://www.filevanta.com/s/qx83kdm2/home.docx?dl=0

WHAT AM I LOOKING FOR?
A clean, well designed theme.

Here is a link to the logo:
https://www.filevanta.com/s/mr47tpz9/logo%20-%20horizontal.tif?dl=0
-----------------------------------------
Here are a few sites I like the design of and what I like about them:
www.quenbrook.com-all around my favorite, beautiful graphics, clean layout, bold use of colors on a dark background
Ravelto.com- clean layout, The use of humans and bubble style elements.
Mintharbor.com :) clean, bold, unique pop art style but professional
plumevault.com - From the unique colors and artwork and the ability of that art to not interfere with the important elements of the site
sparkwidgets.com-clean, nice colors, well organized and separated sections.
www.dunmereco.com-love the font, use of colors and sectionalized style

All in all, I am not picky and open to so many styles. I would ultimately like the designer I pick to design all 21 pages.
Updates

Hello everyone,Moving forward, I would like you all to pay special attention to the section in my brief titled "Here are a few sites I like the design of and what I like about them". Please see below, I handpicked each one of these as sites I really like. Thank you.Here are a few sites I like the design of and what I like about them:Ravelto.com- clean layout, The use of humans and bubble style elements.Mintharbor.com :) clean, bold, unique pop art style but professionalwriteraccess.com - From the unique colors and artwork and the ability of that art to not interfere with the important elements of the sitegrowthgeeks.com-clean, nice colors, well organized and separated sections.www.dunmereco.com-love the font, use of colors and sectionalized stylewww.quenbrook.com-beautiful graphics, clean layout, bold use of colors----------------------------------------- Added Tuesday, November 24, 2015

I updated the homepage, you can see it here:https://www.dropbox.com/s/kwlkbsookq3cg2m/1new%20homepage.docx?dl=0I am modeling it after my favorite designed site: triplelift.comI love the dark colors with the orange glowing style boldness of the buttons. It's real clean too. Added Tuesday, November 24, 2015

Target Market(s)

small business owners, marketers, freelancer writers, graphic designers,

Industry/Entity Type

Building

Number of Pages Required

5+ page

Requirements
Must have
• I can't think of anything the project must have.
Nice to have
• WHAT AM I LOOKING FOR?
• A clean, well designed theme. I had a designer do a bit of work putting elements together, I found it to be very plain, but I like the Application Page (https://www.filevanta.com/s/jb19ckr3/Pelmora-Website.ai?dl=0)
• Here is a link to the logo:
• https://www.filevanta.com/s/mr47tpz9/logo%20-%20horizontal.tif?dl=0
• Here are a few sites I like the design of and what I like about them:
• Ravelto.com- clean layout, The use of humans and bubble style elements.
• Mintharbor.com :) clean, bold, unique pop art style but professional
• plumevault.com - From the unique colors and artwork and the ability of that art to not interfere with the important elements of the site
• sparkwidgets.com-clean, nice colors, well organized and separated sections.
• www.dunmereco.com-love the font, use of colors and sectionalized style
• www.quenbrook.com-beautiful graphics, clean layout, bold use of colors
• -----------------------------------------
Should not have
• out of the boxed, templated style website. I want this site to be memorable and not look like a thousand others

```html
<!DOCTYPE html>
<html lang="en">
<head>
<meta charset="utf-8">
<title>Pelmora – Experts collaborating on your project</title>
<link rel="stylesheet" href="https://fonts.googleapis.com/css2?family=Roboto:ital,wght@0,300;0,400;0,500;0,700;1,400&display=swap">
<style>
:root{
  --orange:#f7941d;
  --teal:#3b9dba;
  --teal-light:#7cc2d6;
  --green:#3aa317;
  --ink:#333;
  --muted:#666;
  --panel:#f4f4f4;
  --dark:#1d2024;
  --footer:#72bcd4;
  --white:#fff;
}
*{box-sizing:border-box;margin:0;padding:0}
html,body{width:866px;height:1200px;overflow:hidden}
body{font-family:'Roboto',sans-serif;color:var(--ink);background:var(--white);position:relative}
.abs{position:absolute}

/* header */
.site-header{position:absolute;left:0;top:0;width:866px;height:73px;background:var(--white);box-shadow:0 1px 3px rgba(0,0,0,.08);z-index:2}
.brand{left:54px;top:22px;display:flex;align-items:center;gap:6px}
.brand-name{font-size:20px;font-weight:500;color:var(--orange);letter-spacing:.2px}
.brand-dot{width:26px;height:26px;border-radius:50%;background:var(--orange)}
.search{left:246px;top:22px;width:178px;height:29px;border:1px solid #ccc;border-radius:2px;display:flex;align-items:center;padding-left:10px;gap:8px;font-size:11px;color:#999}
.main-nav{left:462px;top:32px;display:flex;gap:18px;font-size:9.5px;font-weight:500;color:#444;letter-spacing:.2px}
.bell{left:703px;top:30px}
.bell-count{left:710px;top:20px;width:12px;height:12px;border-radius:50%;background:var(--teal);color:#fff;font-size:8px;text-align:center;line-height:12px}
.account-btn{left:728px;top:22px;width:85px;height:29px;background:var(--orange);color:#fff;font-size:9.5px;font-weight:500;display:flex;align-items:center;justify-content:center}

/* hero */
.hero{position:absolute;left:0;top:73px;width:866px;height:361px;background:linear-gradient(90deg,#cfe7ea 0%,#c4e0e6 35%,#a9c9d6 60%,#7e9ab0 100%);overflow:hidden}
.hero-photo{position:absolute;left:280px;top:0;width:586px;height:361px;background:linear-gradient(180deg,rgba(160,200,215,.35),rgba(60,80,110,.45))}
.hero-title{left:52px;top:78px;font-size:41px;line-height:38px;font-weight:400;color:var(--teal);letter-spacing:.5px}
.hero-sub{left:54px;top:160px;font-size:16px;line-height:20px;color:#333;font-weight:400}
.cta{left:54px;top:218px;width:110px;height:36px;background:var(--green);color:#fff;font-size:15px;font-weight:500;display:flex;align-items:center;justify-content:center}
.dots{left:54px;top:313px;display:flex;gap:6px}
.dots i{width:9px;height:9px;border-radius:50%;background:#666}
.dots i:first-child{background:var(--teal)}
.role-bubble{position:absolute;color:#fff;font-size:12px;font-weight:500;text-align:center;line-height:13px}

/* projects */
.projects{position:absolute;left:0;top:434px;width:866px;height:269px;background:var(--panel)}
.filters-title{left:54px;top:36px;font-size:12px;font-weight:500;display:flex;align-items:center;gap:7px}
.price{left:54px;top:59px;width:156px;font-size:10px;color:#555;display:flex;justify-content:space-between}
.slider{left:54px;top:80px;width:156px;height:3px;background:var(--teal-light)}
.slider-knob{left:58px;top:75px;width:12px;height:12px;border-radius:50%;background:var(--orange)}
.filter-list{left:54px;top:98px;list-style:none;font-size:10px;color:#444}
.filter-list li{height:22.6px;display:flex;align-items:center;gap:10px}
.filter-list li::before{content:"";border-left:4px solid #555;border-top:3px solid transparent;border-bottom:3px solid transparent}
.section-title{left:247px;top:35px;font-size:13.5px;font-weight:500}
.sort{right:53px;top:38px;font-size:9.5px;color:#333}
.sort b{color:var(--orange);font-weight:500}
.card{position:absolute;width:279px;height:85px;background:#fff}
.card-photo{position:absolute;left:14px;top:16px;width:52px;height:52px;background:linear-gradient(135deg,#d9c8bb,#8c7b70)}
.card-text{position:absolute;left:81px;top:14px;width:190px;font-size:9.5px;line-height:16px;color:#333}
.card-meta{position:absolute;left:81px;top:56px;font-size:9.5px;color:var(--teal);white-space:nowrap}

/* testimonials */
.testimonials{position:absolute;left:0;top:703px;width:866px;height:237px;background:linear-gradient(90deg,#15181b,#2a2e33 50%,#15181b)}
.testimonials h2{position:absolute;left:0;width:866px;top:23px;text-align:center;font-size:13.5px;font-weight:500;color:var(--teal)}
.quote{position:absolute;top:66px;width:240px}
.avatar{position:absolute;left:0;top:2px;width:42px;height:42px;border-radius:50%;background:linear-gradient(135deg,#f0e0d3,#b79c88);border:2px solid #fff}
.quote p{position:absolute;left:54px;top:0;width:186px;font-size:9px;line-height:18.5px;font-style:italic;color:#ddd}
.quote p::before{content:"“ ";font-weight:700;font-style:normal;color:#fff}
.quote .who{position:absolute;left:54px;top:70px;font-size:9.5px;font-weight:500;color:var(--orange)}
.quote .role{position:absolute;left:54px;top:88px;font-size:8px;font-style:italic;color:#ccc}
.arrows{left:420px;top:204px;display:flex;gap:7px}
.arrows i{width:10px;height:10px;border-radius:50%;background:#fff}

/* press */
.press{position:absolute;left:0;top:940px;width:866px;height:112px;background:var(--panel)}
.press h2{position:absolute;left:0;width:866px;top:32px;text-align:center;font-size:13.5px;font-weight:400;color:#222}
.press-row{position:absolute;left:134px;top:66px;width:600px;display:flex;justify-content:space-between;font-size:13px;font-weight:500;color:#555}

/* footer */
.site-footer{position:absolute;left:0;top:1052px;width:866px;height:148px;background:var(--footer)}
.footer-nav{position:absolute;left:0;width:866px;top:40px;display:flex;justify-content:center;gap:26px;font-size:9.5px;color:#222}
.copyright{position:absolute;left:0;width:866px;top:72px;text-align:center;font-size:9.5px;color:#333}
.social{position:absolute;left:0;width:866px;top:96px;display:flex;justify-content:center;gap:11px}
.social i{width:11px;height:11px;border-radius:50%;background:#222}
</style>
</head>
<body>

<header class="site-header">
  <div class="abs brand"><span class="brand-name">pelmora</span><span class="brand-dot"></span></div>
  <div class="abs search">
    <svg width="10" height="10" viewBox="0 0 10 10"><circle cx="4" cy="4" r="3" fill="none" stroke="#3b9dba" stroke-width="1.4"/><path d="M6.3 6.3 9 9" stroke="#3b9dba" stroke-width="1.4"/></svg>
    <svg width="6" height="4" viewBox="0 0 6 4"><path d="M0 0 3 3 6 0" fill="none" stroke="#999"/></svg>
    Find Freelancers
  </div>
  <nav class="abs main-nav"><span>HOME</span><span>PROJECTS</span><span>HOW IT WORKS</span><span>PLAN</span></nav>
  <svg class="abs bell" width="11" height="12" viewBox="0 0 11 12"><path d="M5.5 0C3 0 2 2 2 4v3L0 9h11L9 7V4C9 2 8 0 5.5 0z M4 10h3a1.5 1.5 0 0 1-3 0z" fill="#555"/></svg>
  <div class="abs bell-count">0</div>
  <div class="abs account-btn">MY ACCOUNT</div>
</header>

<section class="hero">
  <div class="hero-photo" role="img" aria-label="Photo of a team of professionals collaborating around a laptop"></div>
  <h1 class="abs hero-title">Convert More<br>Customers</h1>
  <p class="abs hero-sub">Experience the power of experts<br>collaborating on your project.</p>
  <div class="abs cta">Get Started</div>
  <div class="abs dots"><i></i><i></i><i></i><i></i></div>

  <svg class="abs" style="left:0;top:0" width="866" height="361" aria-hidden="true">
    <g fill="#f7941d">
      <circle cx="391" cy="79" r="44"/><path d="M410 115 425 112 420 98z"/>
      <circle cx="516" cy="51" r="43"/><path d="M535 86 553 80 548 66z"/>
      <circle cx="684" cy="61" r="43"/><path d="M655 92 663 100 668 88z"/>
      <circle cx="244" cy="304" r="43"/><path d="M268 270 284 262 278 280z"/>
    </g>
  </svg>
  <div class="role-bubble" style="left:351px;top:66px;width:80px">Content<br>Marketer</div>
  <div class="role-bubble" style="left:476px;top:38px;width:80px">Graphic<br>Designer</div>
  <div class="role-bubble" style="left:644px;top:48px;width:80px">Creative<br>Writer</div>
  <div class="role-bubble" style="left:204px;top:298px;width:80px">CopyWriter</div>
</section>

<section class="projects">
  <div class="abs filters-title">
    <svg width="8" height="8" viewBox="0 0 8 8"><path d="M0 0h8L5 4v4L3 7V4z" fill="#333"/></svg>Filters
  </div>
  <div class="abs price"><span>Price $20</span><span>$1000</span></div>
  <div class="abs slider"></div>
  <div class="abs slider-knob"></div>
  <ul class="abs filter-list">
    <li>Country</li><li>Categories</li><li>Time Left</li><li>Activate/ Expired</li><li>Contains Adult Content</li><li>Keyword</li><li>Followers</li>
  </ul>

  <h2 class="abs section-title">Crowd Projects</h2>
  <div class="abs sort">Sort: <b>Price</b> &nbsp;| &nbsp; Country &nbsp;| &nbsp; Time left</div>

  <article class="card" style="left:247px;top:68px">
    <div class="card-photo" role="img" aria-label="Portrait of project owner"></div>
    <p class="card-text">Nemo enim ipsam voluptatem voluptas sit aspernatur aut oditaut.</p>
    <p class="card-meta">$ &nbsp;$250 &nbsp;| &nbsp;⌖ U.S &nbsp;| &nbsp;◷ Time Left: 6 days</p>
  </article>
  <article class="card" style="left:534px;top:68px">
    <div class="card-photo" role="img" aria-label="Portrait of project owner"></div>
    <p class="card-text">Nemo enim ipsam voluptatem voluptas sit aspernatur aut oditaut.</p>
    <p class="card-meta">$ &nbsp;$250 &nbsp;| &nbsp;⌖ U.S &nbsp;| &nbsp;◷ Time Left: 6 days</p>
  </article>
  <article class="card" style="left:247px;top:161px">
    <div class="card-photo" role="img" aria-label="Portrait of project owner"></div>
    <p class="card-text">Nemo enim ipsam voluptatem voluptas sit aspernatur aut oditaut.</p>
    <p class="card-meta">$ &nbsp;$250 &nbsp;| &nbsp;⌖ U.S &nbsp;| &nbsp;◷ Time Left: 6 days</p>
  </article>
  <article class="card" style="left:534px;top:161px">
    <div class="card-photo" role="img" aria-label="Portrait of project owner"></div>
    <p class="card-text">Nemo enim ipsam voluptatem voluptas sit aspernatur aut oditaut.</p>
    <p class="card-meta">$ &nbsp;$250 &nbsp;| &nbsp;⌖ U.S &nbsp;| &nbsp;◷ Time Left: 6 days</p>
  </article>
</section>

<section class="testimonials" role="region" aria-label="Testimonials over a dark mosaic of customer photos">
  <h2>Testimonials</h2>
  <div class="quote" style="left:54px">
    <div class="avatar" role="img" aria-label="Customer portrait"></div>
    <p>With Pelmora I have multiple experts perfecting my content and I only pay for the feedback I find valuable. It's perfect..</p>
    <div class="who">-Dana Holt</div><div class="role">CEO, Norvale 9</div>
  </div>
  <div class="quote" style="left:313px">
    <div class="avatar" role="img" aria-label="Customer portrait"></div>
    <p>With Pelmora I have multiple experts perfecting my content and I only pay for the feedback I find valuable. It's perfect..</p>
    <div class="who">-Dana Holt</div><div class="role">CEO, Norvale 9</div>
  </div>
  <div class="quote" style="left:573px">
    <div class="avatar" role="img" aria-label="Customer portrait"></div>
    <p>With Pelmora I have multiple experts perfecting my content and I only pay for the feedback I find valuable. It's perfect..</p>
    <div class="who">-Dana Holt</div><div class="role">CEO, Norvale 9</div>
  </div>
  <div class="abs arrows"><i></i><i></i></div>
</section>

<section class="press">
  <h2>Press Media</h2>
  <div class="press-row"><span>Harbor Ledger</span><span>Corvane</span><span>Tellix</span><span>Market Fold</span><span>Byteline</span><span>Westgate Daily</span></div>
</section>

<footer class="site-footer">
  <nav class="footer-nav"><span>HOME</span><span>PROJECTS</span><span>HOW IT WORKS</span><span>PLAN</span><span>CONTACT</span></nav>
  <p class="copyright">Copyright © 2015. Company Name.All Right Reserved</p>
  <div class="social"><i></i><i></i><i></i><i></i><i></i><i></i></div>
</footer>

</body>
</html>
```